New Business Card Design Project

Use the flyer uploaded and website www.brightoakbuilders.com for inspiration.
List Our Services on Backside of business cards
Marcus Delling
Harborline Builders Inc.
Licensed General Contractors
858-471-6093

Contact Information for Business Card

Use the flyer uploaded and website www.brightoakbuilders.com for inspiration. List Our Services on Backside of business cards Marcus Delling Harborline Builders Inc. Licensed General Contractors 858-471-6093

```html
<!DOCTYPE html>
<html lang="en">
<head>
<meta charset="utf-8">
<title>Harborline Builders – Business Card</title>
<link href="https://fonts.googleapis.com/css2?family=Marcellus&family=Roboto:wght@400;700&display=swap" rel="stylesheet">
<style>
  :root {
    --backdrop: #3b3b3b;
    --card: #141414;
    --edge-blue: #3a86d8;
    --name-blue: #3f8ee0;
    --text-light: #e6e6e6;
    --mark-silver: #d4d4d4;
    --mark-embossed: #2e2e2e;
    --emboss-light: #4a4a4a;
    --icon-red: #d62b2b;
  }
  * { box-sizing: border-box; margin: 0; padding: 0; }
  html, body {
    width: 1200px; height: 801px; overflow: hidden;
    background: var(--backdrop);
  }
  .sheet {
    width: 1200px; height: 801px;
    display: flex; align-items: center; justify-content: center; gap: 40px;
  }
  .card {
    width: 540px; height: 310px;
    background: var(--card);
    border-bottom: 3px solid var(--edge-blue);
    border-left: 2px solid var(--edge-blue);
    position: relative;
    overflow: hidden;
  }
  .brand-block {
    position: absolute; left: 24px; top: 178px;
    width: 226px;
    text-align: center;
  }
  .brand-name {
    font-family: "Marcellus", serif;
    font-size: 19px; letter-spacing: 1px;
    color: var(--mark-silver);
    white-space: nowrap;
  }
  .divider {
    position: absolute; left: 272px; top: 110px;
    width: 1px; height: 120px; background: var(--edge-blue);
  }
  .contact-block {
    position: absolute; left: 292px; top: 36px;
    font-family: "Roboto", sans-serif; color: var(--text-light);
  }
  .person-name { font-weight: 700; font-size: 19px; color: var(--name-blue); }
  .person-title { font-size: 14px; margin-top: 3px; }
  .company-name { font-size: 14px; margin-top: 24px; }
  .contact-list { list-style: none; margin-top: 22px; font-size: 14px; }
  .contact-list li { display: flex; align-items: center; gap: 8px; margin-bottom: 7px; }
  .contact-list svg { width: 13px; height: 13px; flex: none; }
  .card-back .brand-block {
    left: 0; width: 100%; top: 160px;
  }
  .card-back .brand-name {
    font-size: 34px; letter-spacing: 2px;
    color: var(--mark-embossed);
    text-shadow: 1px 1px 0 var(--emboss-light), -1px -1px 0 #0a0a0a;
  }
</style>
</head>
<body>
<main class="sheet">
  <section class="card card-front" aria-label="Card front">
    <div class="brand-block"><span class="brand-name">HARBORLINE BUILDERS</span></div>
    <div class="divider"></div>
    <div class="contact-block">
      <p class="person-name">MARCUS DELLING</p>
      <p class="person-title">Licensed General Contractors</p>
      <p class="company-name">Harborline Builders Inc.</p>
      <ul class="contact-list">
        <li>
          <svg viewBox="0 0 16 16" aria-hidden="true"><circle cx="8" cy="8" r="8" fill="var(--icon-red)"/><path d="M5 4.5c.6-.4 1.2-.2 1.5.4l.5 1c.2.4 0 .8-.3 1l-.4.3c.4.9 1.1 1.6 2 2l.3-.4c.2-.3.6-.5 1-.3l1 .5c.6.3.8.9.4 1.5-.5.8-1.4 1-2.2.6-1.8-.8-3.2-2.2-4-4-.4-.8-.2-1.700.2-2.6z" fill="#fff"/></svg>
          858-471-6093
        </li>
        <li>
          <svg viewBox="0 0 16 16" aria-hidden="true"><circle cx="8" cy="8" r="8" fill="var(--icon-red)"/><circle cx="8" cy="8" r="4.5" fill="none" stroke="#fff" stroke-width="1.2"/><path d="M3.5 8h9M8 3.5c-1.5 1.5-1.5 7.5 0 9M8 3.5c1.5 1.5 1.5 7.5 0 9" fill="none" stroke="#fff" stroke-width="1"/></svg>
          www.brightoakbuilders.com
        </li>
      </ul>
    </div>
  </section>
  <section class="card card-back" aria-label="Card back">
    <div class="brand-block"><span class="brand-name">HARBORLINE BUILDERS</span></div>
  </section>
</main>
</body>
</html>
```